Web design for Crowdfunding site HopeWingsRally.com

We need a web design for christian crowdfunding website. Here is the challenge: We need responsive layout that is targeted first in iPad size of screen. It should also scale somehow down to iPhone size of screens. Web layout can be about the same size as iPad screen.

Screens should work so that main page scrolls not but only certain part of the screen scrolls and always one "page" at time. We can implement these "scrolls" then later with javascript but now we need only design. The challenge is to create this kind of hybrid website / app look.

Target is at first to raise funds to orphan people needing about $40 per month for their living and education. There is always some organization which takes care of these kids. Later there will be other christian missions included. At first we are looking to find monthly supporters.

You can be as creative as you want :) As you see from the look and feel sector, I am not looking any same traditional look which many "help kids" sites have. I am looking to reach now younger generation and therefore iPad and mobile are the main screen sizes.

Inspirational designs:
- https://example-gallery.test/profiles/studiofernlake/designs/482716?from=%2Fbrowse%2Fxhr%2Fdesigns%3Fcategory%3Dmobile-app-design
- http://www.artpoolhub.test/design/8261047 Clear, simple visuals
- http://www.artpoolhub.test/design/7394215 Header
- http://www.artpoolhub.test/design/6048392 Contrast in the colors, i think is powerfull

Some terms could be: Kids play, kids are learning (in the school). No static posture but living like kids are. I wonder also how we could also add little bit gaming style even though the question is of reali life of real people. Giving should be rewarding.

Target Market(s)

People who want help other people.

Industry/Entity Type

Christian

Number of Pages Required

4 page

Requirements
Must have
• Homepage. Mission page (In my wireframes it was one kid).
Nice to have
• Other pages and some idea how to scroll. 4 pages is no must. If you feel easy, please give first some draft and I give comments on that.

```html
<!DOCTYPE html>
<html lang="en">
<head>
<meta charset="utf-8">
<title>Hope Wings Rally Website – About Tablet View</title>
<link rel="stylesheet" href="https://fonts.googleapis.com/css2?family=Orbitron:wght@700&family=Exo+2:wght@500;600&family=Lato:wght@400;700&display=swap">
<style>
  :root {
    --page-bg: #c8d1dd;
    --title-grey: #6e6b6b;
    --screen-white: #ffffff;
    --screen-soft: #f5f5f5;
    --band-blue: #2f8fcf;
    --text-dark: #3a3a3a;
    --text-body: #2b2b2b;
    --accent-green: #35c98c;
    --accent-yellow: #f2c12e;
    --accent-red: #e8553f;
    --icon-blue: #8fbcdc;
    --hero-dark: #2a3d5a;
    --hero-warm: #b99a86;
  }
  * { margin: 0; padding: 0; box-sizing: border-box; }
  html, body { width: 1200px; height: 1089px; overflow: hidden; }
  body { background: var(--page-bg); font-family: "Lato", Arial, sans-serif; position: relative; }

  .sheet-title {
    position: absolute; left: 0; top: 62px; width: 1200px; text-align: center;
    font-family: "Orbitron", sans-serif; font-weight: 700; font-size: 37px; line-height: 42px;
    letter-spacing: 2px; color: var(--title-grey); text-transform: uppercase;
  }

  .screen { position: absolute; left: 351px; width: 500px; height: 312px; overflow: hidden; box-shadow: 0 4px 14px rgba(0,0,0,.18); }
  .screen--about { top: 216px; background: var(--screen-white); }
  .screen--how { top: 644px; background: var(--screen-soft); }

  .hero { position: absolute; left: 0; top: 0; width: 500px; height: 138px;
    background: linear-gradient(90deg, var(--hero-warm) 0%, #8a7d7a 45%, var(--hero-dark) 100%); }
  .hero__title { position: absolute; top: 50px; width: 100%; text-align: center; color: #fff;
    font-family: "Orbitron", sans-serif; font-weight: 700; font-size: 15px; letter-spacing: .5px; }
  .hero__rule { position: absolute; top: 73px; left: 236px; width: 28px; height: 2px; background: var(--accent-yellow); }
  .hero__lead { position: absolute; top: 79px; left: 175px; width: 150px; text-align: center; color: #fff;
    font-size: 6px; font-weight: 700; line-height: 9px; }

  .crumb-bar { position: absolute; left: 0; top: 138px; width: 500px; height: 28px; background: var(--band-blue);
    color: #fff; font-size: 6px; font-weight: 700; display: flex; align-items: center; padding: 0 30px 0 32px; }
  .crumb-bar__home { width: 11px; height: 10px; margin-right: 6px; }
  .crumb-bar__path { flex: 1; display: flex; align-items: center; gap: 4px; }
  .crumb-bar__links { display: flex; align-items: center; gap: 7px; }
  .crumb-bar__divider { width: 1px; height: 14px; background: #fff; }

  .intro { position: absolute; left: 32px; top: 186px; width: 270px; }
  .intro__heading { font-family: "Exo 2", sans-serif; font-weight: 600; font-size: 15px; color: var(--text-dark); margin-bottom: 7px; }
  .intro__text { font-size: 5.6px; line-height: 10px; color: var(--text-body); font-weight: 700; margin-bottom: 8px; }
  .intro__button { display: inline-block; width: 102px; height: 20px; line-height: 20px; text-align: center;
    background: var(--accent-green); color: #fff; font-size: 6px; font-weight: 700; }
  .intro__photo { position: absolute; left: 314px; top: 190px; width: 156px; height: 114px;
    background: linear-gradient(135deg, #6b4a3a 0%, #c9a583 50%, #e9e2da 100%); }

  .how__heading { position: absolute; top: 52px; width: 100%; text-align: center;
    font-family: "Exo 2", sans-serif; font-weight: 600; font-size: 17px; color: var(--text-dark); letter-spacing: .5px; }
  .step { position: absolute; top: 100px; width: 140px; text-align: center; }
  .step__icon { display: block; margin: 0 auto; width: 58px; height: 58px; }
  .step__label { margin-top: 16px; font-family: "Exo 2", sans-serif; font-weight: 600; font-size: 8px; color: var(--text-dark); text-transform: uppercase; }
  .step__rule { width: 32px; height: 1.5px; margin: 5px auto 6px; }
  .step__text { font-size: 6px; font-weight: 700; line-height: 10px; color: var(--text-body); }
  .step--idea { left: 9px; } .step--share { left: 173px; } .step--funds { left: 338px; }
  .join { position: absolute; top: 119px; width: 22px; height: 22px; }
  .join--one { left: 150px; } .join--two { left: 315px; }
</style>
</head>
<body>
  <h1 class="sheet-title">Hope Wings Rally Website<br>About Tablet View</h1>

  <section class="screen screen--about">
    <div class="hero" role="img" aria-label="Photo of a mother holding her baby at home"></div>
    <h2 class="hero__title">ABOUT US</h2>
    <span class="hero__rule"></span>
    <p class="hero__lead">Pellentesque pharetra sapien non quam placerat vestibulum.</p>

    <nav class="crumb-bar">
      <svg class="crumb-bar__home" viewBox="0 0 12 11"><path d="M6 0 0 5.5h1.6V11h3.2V7.5h2.4V11h3.2V5.5H12z" fill="#fff"/></svg>
      <span class="crumb-bar__path">You Are Here: Home
        <svg width="5" height="7" viewBox="0 0 5 7"><path d="M1 0.5 4 3.5 1 6.5" stroke="#fff" stroke-width="1.3" fill="none"/></svg>
        About Us</span>
      <span class="crumb-bar__links">Who We Are <span class="crumb-bar__divider"></span> How It Works</span>
    </nav>

    <article class="intro">
      <h3 class="intro__heading">Who We Are</h3>
      <p class="intro__text">Pellentesque pharetra sapien non quam placerat vestibulum. Aliquam dignissim ex nec feugiat condimentum. Sed iaculis magna mi, sed semper ex semper eu. Etiam sagittis ante eget nisl tempus.</p>
      <p class="intro__text">Maecenas facilisis sollicitudin magna at fringilla. Pellentesque pharetra sapien non quam placerat vestibulum. Aliquam dignissim ex nec feugiat condimentum. Sed iaculis magna mi, sed semper ex semper eu. Vestibulum auctor mi sed.</p>
      <span class="intro__button">Become a Volunteer</span>
    </article>
    <div class="intro__photo" role="img" aria-label="Photo of a mother playing with her toddler and toy cars on the floor"></div>
  </section>

  <section class="screen screen--how">
    <h2 class="how__heading">How it Works ?</h2>

    <div class="step step--idea">
      <svg class="step__icon" viewBox="0 0 58 58" fill="none" stroke="var(--icon-blue)" stroke-width="1.2">
        <circle cx="29" cy="29" r="28"/>
        <path d="M29 21a6 6 0 0 0-3.5 10.9V35h7v-3.1A6 6 0 0 0 29 21z"/>
        <path d="M26 37h6M27 39h4M29 17v-2M21 21l-1.5-1.5M37 21l1.5-1.5M19 28h-2M39 28h2"/>
      </svg>
      <p class="step__label">Send your idead</p>
      <div class="step__rule" style="background:var(--accent-green)"></div>
      <p class="step__text">Pellentesque pharetra sapien non<br>quam placerat vestibulum.</p>
    </div>

    <svg class="join join--one" viewBox="0 0 22 22"><path d="M8 0h6v8h8v6h-8v8H8v-8H0V8h8z" fill="var(--accent-green)"/><path d="M8 8h6v6H8z" fill="var(--band-blue)"/></svg>

    <div class="step step--share">
      <svg class="step__icon" viewBox="0 0 58 58" fill="none" stroke="var(--icon-blue)" stroke-width="1.2">
        <circle cx="29" cy="29" r="28"/>
        <circle cx="29" cy="24" r="5"/>
        <path d="M20 38c0-5 4-8 9-8s9 3 9 8z"/>
        <path d="M35 20a4 4 0 0 1 3 7M39 30c2 1 3 3 3 6"/>
      </svg>
      <p class="step__label">Share with community</p>
      <div class="step__rule" style="background:var(--accent-yellow)"></div>
      <p class="step__text">Pellentesque pharetra sapien non<br>quam placerat vestibulum.</p>
    </div>

    <svg class="join join--two" viewBox="0 0 22 22"><path d="M8 0h6v8h8v6h-8v8H8v-8H0V8h8z" fill="var(--accent-green)"/><path d="M8 8h6v6H8z" fill="var(--band-blue)"/></svg>

    <div class="step step--funds">
      <svg class="step__icon" viewBox="0 0 58 58" fill="none" stroke="var(--icon-blue)" stroke-width="1.2">
        <circle cx="29" cy="29" r="28"/>
        <rect x="27" y="18" width="12" height="20" rx="1"/>
        <path d="M30 23h6M30 27h6M30 31h6"/>
        <path d="M21 19v17l1.5 3 1.5-3V19z"/>
      </svg>
      <p class="step__label">Collect fundz</p>
      <div class="step__rule" style="background:var(--accent-red)"></div>
      <p class="step__text">Pellentesque pharetra sapien non<br>quam placerat vestibulum.</p>
    </div>
  </section>
</body>
</html>
```